Cobalt Ridge Electric Needs A Logo Design

We need a logo for my new company based out of Sacramento, Ca called Cobalt Ridge Electric. The name says it all, my electrical contracting business provides "Cobalt Ridge Professional Work" I'm open to any colors that pop and customers to say Wow. I would love to print my cards on metal.

Industry/Entity Type

Business

Contact Information for Business Card

The card needs to have as follows
Name of company: Cobalt Ridge Electric
My Name: Marco Delvane
Phone # 916-555-0173
CL# 2049381
Email: cobaltridgeelectric@mailnest.example
and a slogan that represent "COBALT RIDGE"

Requirements
Must have
• The card needs to have as follows
• Name of company: Cobalt Ridge Electric
• My Name : Marco Delvane
• Phone # 916-555-0173
• CL# 2049381
• Email: cobaltridgeelectric@mailnest.example
• and a slogan that represent "COBALT RIDGE"
Nice to have
• popping colors
• electrical Arcing

```html
<!DOCTYPE html>
<html lang="en">
<head>
<meta charset="utf-8">
<title>Cobalt Ridge Electric – Business Card</title>
<link rel="stylesheet" href="https://fonts.googleapis.com/css2?family=Montserrat:wght@400;500;700&display=swap">
<style>
  :root {
    --page-bg: #e9e7e3;
    --card-bg: #ffffff;
    --ink-grey: #5b5e63;
    --brand-red: #e3323f;
    --brand-blue: #2aa6dc;
    --card-shadow: rgba(0, 0, 0, 0.18);
  }
  * { box-sizing: border-box; margin: 0; padding: 0; }
  html, body {
    width: 1200px;
    height: 1022px;
    overflow: hidden;
    background: var(--page-bg);
  }
  body {
    display: flex;
    align-items: center;
    justify-content: center;
    font-family: "Montserrat", Arial, sans-serif;
  }
  .business-card {
    position: relative;
    width: 1000px;
    height: 570px;
    background: var(--card-bg);
    box-shadow: 0 18px 40px var(--card-shadow);
  }
  .brand-block {
    position: absolute;
    top: 66px;
    right: 80px;
    display: flex;
    align-items: center;
    gap: 22px;
  }
  .brand-square {
    width: 72px;
    height: 72px;
    flex: none;
    background: var(--brand-blue);
  }
  .brand-text {
    display: flex;
    flex-direction: column;
  }
  .brand-name {
    color: var(--ink-grey);
    font-weight: 500;
    font-size: 46px;
    line-height: 1.02;
    letter-spacing: 0.5px;
    text-transform: uppercase;
  }
  .brand-slogan {
    margin-top: 10px;
    color: var(--ink-grey);
    font-weight: 400;
    font-size: 18px;
    letter-spacing: 1px;
  }
  .holder-name {
    position: absolute;
    left: 80px;
    top: 264px;
    color: var(--brand-red);
    font-weight: 700;
    font-size: 42px;
    line-height: 1.2;
    letter-spacing: 1px;
    text-transform: uppercase;
  }
  .divider-line {
    position: absolute;
    left: 80px;
    right: 80px;
    top: 320px;
    height: 3px;
    background: var(--brand-blue);
  }
  .contact-list {
    position: absolute;
    left: 80px;
    top: 346px;
    list-style: none;
    display: flex;
    flex-direction: column;
    gap: 10px;
  }
  .contact-item {
    display: flex;
    align-items: center;
    gap: 16px;
    color: var(--ink-grey);
    font-size: 27px;
    font-weight: 400;
    line-height: 1.25;
  }
  .contact-icon {
    width: 24px;
    height: 24px;
    flex: none;
  }
</style>
</head>
<body>
  <article class="business-card">
    <header class="brand-block">
      <span class="brand-square" aria-hidden="true"></span>
      <div class="brand-text">
        <h1 class="brand-name">Cobalt Ridge<br>Electric</h1>
        <p class="brand-slogan">Cobalt Ridge Professional Work</p>
      </div>
    </header>

    <h2 class="holder-name">Marco Delvane</h2>
    <div class="divider-line" aria-hidden="true"></div>

    <ul class="contact-list">
      <li class="contact-item">
        <svg class="contact-icon" viewBox="0 0 24 24" aria-hidden="true">
          <rect x="2" y="5" width="20" height="14" rx="2" fill="none" stroke="#2aa6dc" stroke-width="2"/>
          <line x1="6" y1="10" x2="18" y2="10" stroke="#2aa6dc" stroke-width="2"/>
          <line x1="6" y1="14" x2="13" y2="14" stroke="#2aa6dc" stroke-width="2"/>
        </svg>
        <span>2049381</span>
      </li>
      <li class="contact-item">
        <svg class="contact-icon" viewBox="0 0 24 24" aria-hidden="true">
          <path d="M6 3 L10 3 L11 8 L8.5 9.5 C9.7 12 12 14.3 14.5 15.5 L16 13 L21 14 L21 18 C21 19.5 19.5 21 18 21 C10 20 4 14 3 6 C3 4.5 4.5 3 6 3 Z" fill="none" stroke="#2aa6dc" stroke-width="2" stroke-linejoin="round"/>
        </svg>
        <span>916-555-0173</span>
      </li>
      <li class="contact-item">
        <svg class="contact-icon" viewBox="0 0 24 24" aria-hidden="true">
          <rect x="2" y="5" width="20" height="14" rx="2" fill="none" stroke="#2aa6dc" stroke-width="2"/>
          <polyline points="3,6 12,13 21,6" fill="none" stroke="#2aa6dc" stroke-width="2"/>
        </svg>
        <span>cobaltridgeelectric@mailnest.example</span>
      </li>
    </ul>
  </article>
</body>
</html>
```